Non fiction book cover. The book advises how to get a new job.

The book size will be 20cm high by 13cm wide and I need a front cover which can wrap around to the back. This book has a serious message, but I've tried to make it quite light to read and accessible. So I don't want a cover that is too dour or serious and not frivolous either. At the end of the project, I will need a high resolution 3D image of the book, included as part of the package.<br/>The Title of the book is:- "Past Sixty? Hunting for your final post?<br/>by Gareth Millbrook-Ashdown".<br/>I am thinking of a light yellow background, with a striking image to attract attention. The image and words should be clear and sharp.<br/>Here is the, BACK COVER wording.<br/>"This book tells you clearly and simply the steps that you need to take, to get a job, once you’re over 50.<br/>It advises you on the techniques to use to write a killer CV.<br/>It explains how to ensure that your CV attention.<br/>It shows the best way to approach your local job agency.<br/>It demonstrates the best way to use your network.<br/><br/>This book, written by someone with 30 years’ experience in the recruitment industry, gives you ALL the answers.<br/>Whether you are a top executive or someone after some local part time work, then this book is for you. <br/>With the help of this book you will secure your next position.<br/>

Target Market(s)

UK, over 50s, male and female.

Font styles to use
Serif

Colors
fbee3e

Requirements
Must have
• A clear uncluttered cover.
Should not have
• Fussy and over complicated

```html
<!DOCTYPE html>
<html lang="en">
<head>
<meta charset="utf-8">
<title>Past Sixty? Hunting for your final post? – Book Cover</title>
<link href="https://fonts.googleapis.com/css2?family=Bebas+Neue&family=Nunito:wght@900&family=Cinzel:wght@700&family=EB+Garamond:ital,wght@0,400;1,700&display=swap" rel="stylesheet">
<style>
  :root {
    --page: #ffffff;
    --cover-yellow: #f9eb46;
    --cover-yellow-light: #fbf08a;
    --title-red: #d93445;
    --title-teal: #43b59b;
    --band-teal: #45c1a8;
    --ink: #1f1f1f;
    --peak-teal: #3dbb9f;
    --peak-pink: #e8737a;
    --cloud-blue: #18c6c9;
  }
  * { box-sizing: border-box; margin: 0; padding: 0; }
  html, body { width: 1200px; height: 800px; overflow: hidden; background: var(--page); }
  .spread {
    position: relative; width: 1200px; height: 800px;
    display: flex; justify-content: center; align-items: center; gap: 30px;
  }
  .cover {
    position: relative; width: 455px; height: 700px; overflow: hidden;
    background: linear-gradient(160deg, var(--cover-yellow-light) 0%, var(--cover-yellow) 45%);
    box-shadow: 0 6px 20px rgba(0,0,0,.18);
  }
  .band {
    position: absolute; left: 0; right: 0; bottom: 0; height: 80px;
    background: var(--band-teal);
    display: flex; align-items: center; justify-content: center;
  }
  .author {
    font-family: 'Cinzel', serif; font-weight: 700; font-size: 22px;
    letter-spacing: 1px; color: var(--ink);
  }
  /* Front */
  .front-title { position: absolute; top: 42px; left: 0; right: 0; text-align: center; }
  .kicker {
    font-family: 'Nunito', sans-serif; font-weight: 900; font-size: 54px;
    color: var(--title-teal); line-height: 1; letter-spacing: 1px;
  }
  .headline {
    font-family: 'Bebas Neue', sans-serif; font-size: 96px; line-height: .86;
    color: var(--title-red); margin-top: 10px;
    text-shadow: 0 0 14px rgba(255,255,255,.8);
  }
  .front-art {
    position: absolute; left: 0; right: 0; bottom: 80px; height: 250px;
    background: linear-gradient(180deg, rgba(249,235,70,0) 0%, rgba(232,115,122,.45) 55%, var(--peak-teal) 100%);
  }
  /* Back */
  .back-inner { position: absolute; top: 36px; left: 36px; right: 36px; }
  .back-kicker {
    font-family: 'Nunito', sans-serif; font-weight: 900; font-size: 26px;
    color: var(--title-teal); text-align: center; line-height: 1;
  }
  .back-headline {
    font-family: 'Bebas Neue', sans-serif; font-size: 38px; line-height: .95;
    color: var(--title-red); text-align: center; margin-top: 4px;
  }
  .back-copy {
    font-family: 'EB Garamond', serif; color: var(--ink);
    font-size: 14.5px; line-height: 1.3; margin-top: 14px;
  }
  .back-copy .lead { font-size: 16px; margin-bottom: 8px; }
  .points { list-style: none; margin-bottom: 10px; }
  .points li {
    font-style: italic; font-weight: 700; position: relative;
    padding-left: 20px; margin-bottom: 5px;
  }
  .points li::before {
    content: ""; position: absolute; left: 2px; top: 7px;
    width: 7px; height: 7px; border-radius: 50%; background: var(--ink);
  }
  .back-copy p { margin-bottom: 9px; text-align: justify; }
  .back-art {
    position: absolute; left: 36px; width: 190px; bottom: 80px; height: 110px;
    background: linear-gradient(180deg, rgba(249,235,70,0) 0%, rgba(232,115,122,.45) 55%, var(--peak-teal) 100%);
  }
</style>
</head>
<body>
<main class="spread">
  <section class="cover cover-back" aria-label="Back cover">
    <div class="back-inner">
      <div class="back-kicker">PAST SIXTY?</div>
      <div class="back-headline">HUNTING FOR YOUR FINAL POST?</div>
      <div class="back-copy">
        <p class="lead">'It explains how to find work, clearly and simply, past sixty.'</p>
        <ul class="points">
          <li>It gives you all the techniques for a killer CV.</li>
          <li>It explains how to ensure your CV gets attention.</li>
          <li>It advises you how to approach your local agency.</li>
          <li>It guides you through making effective use of your network.</li>
        </ul>
        <p>This book, written by a top recruiter with 30 years' recruitment experience, gives you all the answers you need, up to date and developed from a lifetime of real placements that helped his candidates to secure their roles.</p>
        <p>Whether you are a top executive or after some local part-time work, this book is for you, with a proven application formula and a clear cycle to follow.</p>
        <p>This book will help you to secure your next position.</p>
      </div>
    </div>
    <div class="back-art" role="img" aria-label="Small illustration of a job seeker sitting on a teal and pink mountain peak with clouds"></div>
    <div class="band"></div>
  </section>

  <section class="cover cover-front" aria-label="Front cover">
    <div class="front-title">
      <div class="kicker">PAST SIXTY?</div>
      <h1 class="headline">HUNTING FOR<br>YOUR FINAL<br>POST?</h1>
    </div>
    <div class="front-art" role="img" aria-label="Illustration of a job seeker with a backpack sitting on top of teal and pink geometric mountains, with pink and blue clouds"></div>
    <div class="band"><span class="author">GARETH MILLBROOK-ASHDOWN</span></div>
  </section>
</main>
</body>
</html>
```